brovlanepass.net

Develop a website for brolanepass.net will be a site to sell tickets for concerts, shows, shows, theaters and others. I need a web design easy view, very easy to use and accumulate events by date. The aim is to develop the site was connected to a complex system that is already developed. (Important this page to a robust system was connected via links the idea is to develop only the front view)
Updates

Reason: I need more designs yet we have not made the decision

Target Market(s)

millennials, adults, who want to enjoy concerts and shows

Industry/Entity Type

Event

Number of Pages Required

5+ page

Colors
1b1b1b
aaaaaa
ffffff

Requirements
Must have
• Easy Vista, accumulation of upcoming events, past events. The tabs should have are: 1 Start: In this part of upcoming events occur. You could put a banner on the top and down the events by date. 2. How to order: page with instructions on how to purchase tickets 3. About Us: The company history 4. Contact: Phones and template for contact by mail 5. Our policies: shopping 6. Notice Privacy: Privacy Notice Copoy 7. Centers Sale: physical places where they can purchase tickets Promoters 8. access: Link to a template
Nice to have
• as you can see p www.quimbarostage.net or farunda.net or farunda.org or gallowmerk.net (important this page to a robust system was connected via links the idea is to develop only the front view)
Should not have
• Many things Tangled

```html
<!DOCTYPE html>
<html lang="en">
<head>
<meta charset="utf-8">
<title>Brovlane Pass</title>
<link href="https://fonts.googleapis.com/css2?family=Roboto+Slab:wght@300;400&family=Roboto:wght@400;500&display=swap" rel="stylesheet">
<style>
:root{
  --ink:#1b1b1b;
  --grey:#aaaaaa;
  --white:#ffffff;
  --text:#555555;
  --soft-bg:#f5f5f5;
  --footer:#262626;
  --card-shade:rgba(95,95,95,.92);
  --date-bg:#2b2b2b;
}
*{margin:0;padding:0;box-sizing:border-box}
html,body{width:840px;height:1200px;overflow:hidden;background:var(--white)}
body{position:relative;font-family:"Roboto",Arial,sans-serif;color:var(--text)}
.slab{font-family:"Roboto Slab",Georgia,serif}

.site-header{position:absolute;left:0;top:0;width:840px;height:60px;background:var(--white)}
.brand{position:absolute;left:60px;top:15px;font-family:"Roboto Slab",Georgia,serif;font-size:22px;color:#333}
.main-nav{position:absolute;right:60px;top:26px;display:flex;gap:27px;font-size:8.5px;color:#444;letter-spacing:.2px}

.hero{position:absolute;left:0;top:60px;width:840px;height:347px;
  background:radial-gradient(ellipse at 50% 25%,#6b5a4e 0%,#3e2e26 45%,#22180f 100%)}
.hero-shade{position:absolute;inset:0;background:rgba(0,0,0,.25)}
.hero-title{position:absolute;left:0;width:840px;top:118px;text-align:center;font-family:"Roboto Slab",Georgia,serif;font-size:35px;color:var(--white)}
.hero-text{position:absolute;left:200px;width:440px;top:170px;text-align:center;font-size:8px;line-height:16px;color:var(--white)}
.hero-btn{position:absolute;left:366px;top:215px;width:108px;height:29px;border:1px solid var(--white);border-radius:3px;
  color:var(--white);font-family:"Roboto Slab",Georgia,serif;font-size:11px;text-align:center;line-height:27px}
.hero-arrow{position:absolute;top:156px;width:37px;height:37px}
.hero-arrow.prev{left:17px}.hero-arrow.next{left:785px}

.welcome{position:absolute;left:0;top:407px;width:840px;height:182px;background:var(--soft-bg);text-align:center}
.section-title{font-family:"Roboto Slab",Georgia,serif;font-size:18px;color:#444;font-weight:400}
.welcome .section-title{margin-top:26px}
.welcome p{width:540px;margin:12px auto 0;font-size:8px;line-height:19.5px;color:#666}
.more-btn{display:inline-block;margin-top:12px;width:144px;height:30px;border:1px solid #bbb;border-radius:2px;
  font-family:"Roboto Slab",Georgia,serif;font-size:8.5px;line-height:28px;color:#777;background:var(--white)}

.events{position:absolute;left:0;top:589px;width:840px;text-align:center}
.events .section-title{margin-top:22px}
.events .lede{margin-top:10px;font-size:8px;color:#666}
.event-card{position:absolute;width:235px;height:160px;overflow:hidden}
.event-card svg{position:absolute;inset:0}
.date-badge{position:absolute;width:68px;height:68px;border-radius:50%;background:var(--date-bg);border:3px solid var(--white);
  color:var(--white);text-align:center;font-family:"Roboto Slab",Georgia,serif}
.date-badge .day{display:block;font-size:25px;line-height:25px;margin-top:8px}
.date-badge .rule{display:block;width:36px;height:1px;background:var(--white);margin:1px auto 0}
.date-badge .month{display:block;font-size:15px;font-style:italic;line-height:17px}
.event-name{position:absolute;font-size:8.6px;font-weight:500;color:var(--white);text-align:right}
.event-link{position:absolute;font-family:"Roboto Slab",Georgia,serif;font-size:7px;font-style:italic;text-decoration:underline;color:var(--white)}
.event-card.featured{text-align:center}
.featured .event-name{left:0;width:235px;text-align:center;top:94px;font-size:9.5px}
.featured .event-blurb{position:absolute;left:20px;width:195px;top:114px;font-size:7.8px;line-height:15px;color:var(--white)}

.site-footer{position:absolute;left:0;top:1036px;width:840px;height:164px;background:var(--footer);text-align:center}
.social{position:absolute;top:23px;left:273px;display:flex;gap:9px}
.social span{width:43px;height:43px;border-radius:50%;border:1px solid #bbb;position:relative}
.footer-rule{position:absolute;left:60px;top:74px;width:720px;height:1px;background:#3c3c3c}
.footer-nav{position:absolute;top:92px;left:0;width:840px;font-family:"Roboto Slab",Georgia,serif;font-size:8.5px;color:#ccc}
.footer-nav i{font-style:normal;margin:0 13px;color:#999}
.copyright{position:absolute;top:121px;left:0;width:840px;font-family:"Roboto Slab",Georgia,serif;font-size:8px;color:#bbb}
</style>
</head>
<body>

<header class="site-header">
  <div class="brand">Brovlane Pass</div>
  <nav class="main-nav">
    <span>HOME</span><span>HOW TO ORDER</span><span>ABOUT US</span><span>CONTACT US</span><span>POLICIES</span><span>PRIVACY</span><span>CENTER SALE</span><span>ACCESS</span>
  </nav>
</header>

<section class="hero" role="img" aria-label="Audience seated in a conference hall facing a speaker and screen">
  <div class="hero-shade"></div>
  <svg class="hero-arrow prev" viewBox="0 0 37 37"><circle cx="18.5" cy="18.5" r="17.5" fill="none" stroke="#fff" stroke-width="2"/><path d="M21 12l-6.5 6.5L21 25" fill="none" stroke="#fff" stroke-width="2.6"/></svg>
  <svg class="hero-arrow next" viewBox="0 0 37 37"><circle cx="18.5" cy="18.5" r="17.5" fill="none" stroke="#fff" stroke-width="2"/><path d="M16 12l6.5 6.5L16 25" fill="none" stroke="#fff" stroke-width="2.6"/></svg>
  <h1 class="hero-title" style="font-weight:400">Brovlane Pass</h1>
  <p class="hero-text">Sed ut perspiciatis unde omnis iste natus error sit voluptatem accusantium doloremque laudantium, totam rem ipsa quae ab illo inventore veritatis et quasi architecto beatae vitae dicta sunt explicabo.</p>
  <div class="hero-btn">Buy TICKET</div>
</section>

<section class="welcome">
  <h2 class="section-title">Welcome to Brovlane Pass</h2>
  <p>Sed ut perspiciatis unde omnis iste natus error sit voluptatem accusantium doloremque laudantium, totam rem aperiam, eaque ipsa quae ab illo inventore veritatis et quasi architecto beatae vitae dicta sunt explicabo. Nemo enim ipsam voluptatem quia voluptas sit aspernatur aut odit aut fugit, sed quia consequuntur magni dolores eos qui ratione voluptatem sequi nesciunt.</p>
  <span class="more-btn">CLICK HERE FOR MORE INFO</span>
</section>

<section class="events">
  <h2 class="section-title">Upcoming Events</h2>
  <p class="lede">Sed ut perspiciatis unde omnis iste natus error sit voluptatem accusantium doloremque laudantium, totam rem aperiam</p>
</section>

<!-- row 1 -->
<article class="event-card" style="left:61px;top:671px">
  <svg viewBox="0 0 235 160" role="img" aria-label="Concert stage with purple lights and a seated crowd"><defs><linearGradient id="g1" x1="0" y1="0" x2="1" y2="1"><stop offset="0" stop-color="#5a2a9a"/><stop offset=".5" stop-color="#2a1e5a"/><stop offset="1" stop-color="#1a1430"/></linearGradient></defs><rect width="235" height="160" fill="url(#g1)"/><polygon points="92,160 235,40 235,160" fill="var(--card-shade)"/></svg>
  <div class="date-badge" style="left:144px;top:54px"><span class="day">09</span><span class="rule"></span><span class="month">mar</span></div>
  <div class="event-name" style="right:10px;top:129px">SED UT PERSPICIATIS</div>
  <div class="event-link" style="right:10px;top:142px">Click Here For More Info &nbsp;»</div>
</article>

<article class="event-card featured" style="left:303px;top:671px">
  <svg viewBox="0 0 235 160" role="img" aria-label="Stage truss under blue light"><defs><linearGradient id="g2" x1="0" y1="0" x2="1" y2="1"><stop offset="0" stop-color="#2a6fc9"/><stop offset=".6" stop-color="#1e56b0"/><stop offset="1" stop-color="#16408a"/></linearGradient></defs><rect width="235" height="160" fill="url(#g2)"/><path d="M216 142c-4 0-6.5 3-6.5 6.3 0 4.5 6.5 10.7 6.5 10.7s6.5-6.2 6.5-10.7c0-3.3-2.5-6.3-6.5-6.3z" transform="translate(0,-8)" fill="#fff"/><circle cx="216" cy="140.5" r="2.2" fill="#1e56b0"/></svg>
  <div class="date-badge" style="left:83px;top:15px"><span class="day">09</span><span class="rule"></span><span class="month">mar</span></div>
  <div class="event-name">SED UT PERSPICIATIS</div>
  <p class="event-blurb">Sed ut perspiciatis unde omnis iste natus error sit voluptatem vitae dicta sunt explicabo.</p>
</article>

<article class="event-card" style="left:545px;top:671px">
  <svg viewBox="0 0 235 160" role="img" aria-label="Crowd with raised hands at a festival under a blue sky"><defs><linearGradient id="g3" x1="0" y1="0" x2="0" y2="1"><stop offset="0" stop-color="#6f8fd0"/><stop offset=".5" stop-color="#3b3f66"/><stop offset="1" stop-color="#141420"/></linearGradient></defs><rect width="235" height="160" fill="url(#g3)"/><polygon points="92,160 235,40 235,160" fill="var(--card-shade)"/></svg>
  <div class="date-badge" style="left:144px;top:54px"><span class="day">09</span><span class="rule"></span><span class="month">mar</span></div>
  <div class="event-name" style="right:10px;top:129px">SED UT PERSPICIATIS</div>
  <div class="event-link" style="right:10px;top:142px">Click Here For More Info &nbsp;»</div>
</article>

<!-- row 2 -->
<article class="event-card" style="left:61px;top:844px">
  <svg viewBox="0 0 235 160" role="img" aria-label="DJ at a mixing desk in cyan and pink light"><defs><linearGradient id="g4" x1="0" y1="0" x2="1" y2="0"><stop offset="0" stop-color="#2fa8b8"/><stop offset=".5" stop-color="#3a5f90"/><stop offset="1" stop-color="#a03aa8"/></linearGradient></defs><rect width="235" height="160" fill="url(#g4)"/><polygon points="92,160 235,40 235,160" fill="var(--card-shade)"/></svg>
  <div class="date-badge" style="left:144px;top:54px"><span class="day">09</span><span class="rule"></span><span class="month">mar</span></div>
  <div class="event-name" style="right:10px;top:129px">SED UT PERSPICIATIS</div>
  <div class="event-link" style="right:10px;top:142px">Click Here For More Info &nbsp;»</div>
</article>

<article class="event-card" style="left:303px;top:844px">
  <svg viewBox="0 0 235 160" role="img" aria-label="Festival crowd dancing in warm sunlight"><defs><linearGradient id="g5" x1="0" y1="0" x2="1" y2="1"><stop offset="0" stop-color="#d9a35a"/><stop offset=".5" stop-color="#b86a48"/><stop offset="1" stop-color="#4a4a6a"/></linearGradient></defs><rect width="235" height="160" fill="url(#g5)"/><polygon points="92,160 235,40 235,160" fill="var(--card-shade)"/></svg>
  <div class="date-badge" style="left:144px;top:54px"><span class="day">09</span><span class="rule"></span><span class="month">mar</span></div>
  <div class="event-name" style="right:10px;top:129px">SED UT PERSPICIATIS</div>
  <div class="event-link" style="right:10px;top:142px">Click Here For More Info &nbsp;»</div>
</article>

<article class="event-card" style="left:545px;top:844px">
  <svg viewBox="0 0 235 160" role="img" aria-label="Speaker in a blue suit addressing an audience"><defs><linearGradient id="g6" x1="0" y1="0" x2="1" y2="0"><stop offset="0" stop-color="#2c3e70"/><stop offset=".5" stop-color="#7a4030"/><stop offset="1" stop-color="#a05a3a"/></linearGradient></defs><rect width="235" height="160" fill="url(#g6)"/><polygon points="92,160 235,40 235,160" fill="var(--card-shade)"/></svg>
  <div class="date-badge" style="left:144px;top:54px"><span class="day">09</span><span class="rule"></span><span class="month">mar</span></div>
  <div class="event-name" style="right:10px;top:129px">SED UT PERSPICIATIS</div>
  <div class="event-link" style="right:10px;top:142px">Click Here For More Info &nbsp;»</div>
</article>

<footer class="site-footer">
  <div class="social">
    <span></span><span></span><span></span><span></span><span></span>
    <span><svg width="43" height="43" viewBox="0 0 43 43" style="position:absolute;left:-1px;top:-1px"><rect x="15.5" y="16.5" width="12" height="9" rx="1" fill="none" stroke="#ddd" stroke-width="1.3"/><path d="M15.5 17l6 4.5 6-4.5" fill="none" stroke="#ddd" stroke-width="1.3"/></svg></span>
  </div>
  <div class="footer-rule"></div>
  <nav class="footer-nav">HOME<i>|</i>HOW TO ORDER<i>|</i>ABOUT US<i>|</i>CONTACT US<i>|</i>POLICIES<i>|</i>PRIVACY<i>|</i>CENTER SALE<i>|</i>ACCESS</nav>
  <p class="copyright">© Copyrights 2017 Brovlane Pass..All Rights Reserved.</p>
</footer>

</body>
</html>
```